Beekeeper needs a label for honey jars

Ciao! I'm from Como Italy
I'm a hobbyist beekeeper and I produce honey for myself and my friends.
I've named my apiary "Dado sereno," a play on words between my nickname (Dado, from Edoardo) and the Italian expression "Dado sereno," which translates to "a drizzle of honey" in English.
I need to create a label for my honey glass jars (250 gr and 500 gr).
I don't need a label for commercial purposes. I would like to include at least the name “Apicoltura Dado sereno", the type of honey (e.g., wildflower, acacia...) and a space for the production year, to be handwritten each year.
In the design some references to the world of bees.
For reference, attached a label with a style I like
Attached are the images of the selected jars and their measurements
Thanks and good job!

Target Market(s)

beekeeping, honey

Requirements
Nice to have
• I would like an elegant style with clean graphics.
Should not have
• Predominance of black color.

```html
<!DOCTYPE html>
<html lang="it">
<head>
<meta charset="utf-8">
<title>Apicoltura Dado sereno – Millefiori</title>
<link rel="stylesheet" href="https://fonts.googleapis.com/css2?family=Oswald:wght@500;600;700&display=swap">
<style>
  :root {
    --paper: #ffffff;
    --comb-tint: #f1f1f3;
    --frame: #7a7a7a;
    --ink-dark: #474747;
    --ink-mid: #555555;
    --ink-soft: #8a8a8a;
    --honey: #e9a43c;
    --lake: #2a90c4;
  }
  * { margin: 0; padding: 0; box-sizing: border-box; }
  html, body {
    width: 1200px; height: 676px; overflow: hidden;
    background: var(--paper);
  }
  .label {
    position: relative; width: 1200px; height: 676px;
    background: var(--paper);
    font-family: "Oswald", "Arial Narrow", sans-serif;
  }
  .comb-backdrop {
    position: absolute; inset: 0;
    background: radial-gradient(ellipse at center, var(--paper) 0%, var(--comb-tint) 100%);
  }
  .frame {
    position: absolute; inset: 0; width: 1200px; height: 676px;
  }
  .line {
    position: absolute; left: 0; right: 0;
    text-align: center; line-height: 1;
    text-transform: uppercase;
  }
  .apiary-kicker {
    top: 53px; font-size: 52px; font-weight: 600;
    color: var(--ink-dark); letter-spacing: 1px;
  }
  .apiary-name {
    top: 104px; font-size: 100px; font-weight: 600;
    color: var(--honey); letter-spacing: 2px;
  }
  .bee-emblem {
    position: absolute; left: 480px; top: 246px;
    width: 240px; height: 202px;
    border-radius: 50% 50% 46% 46%;
    background: radial-gradient(ellipse at center, #f6d6a4 0%, #fbeede 70%, rgba(255,255,255,0) 100%);
  }
  .honey-type {
    top: 487px; font-size: 66px; font-weight: 600;
    color: var(--ink-mid); letter-spacing: 1px;
  }
  .origin {
    top: 568px; font-size: 32px; font-weight: 500;
    color: var(--ink-soft); letter-spacing: 26px;
    padding-left: 26px;
  }
  .lake-band {
    position: absolute; left: 510px; top: 604px;
    width: 178px; height: 24px;
    background: linear-gradient(180deg, #4aa6d3 0%, var(--lake) 100%);
    opacity: .85;
  }
  .fill-in {
    position: absolute; display: flex; align-items: flex-end; gap: 8px;
    font-size: 20px; font-weight: 600; color: var(--ink-mid); line-height: 1;
  }
  .fill-in .blank {
    display: inline-block; height: 3px; background: var(--ink-mid);
    margin-bottom: 3px;
  }
  .weight { left: 91px; top: 620px; }
  .weight .blank { width: 48px; }
  .year { left: 1005px; top: 618px; }
  .year .blank { width: 52px; }
</style>
</head>
<body>
  <main class="label">
    <div class="comb-backdrop" role="img" aria-label="Faint honeycomb hexagon pattern in light grey"></div>

    <svg class="frame" viewBox="0 0 1200 676" aria-hidden="true">
      <rect x="16" y="16" width="1168" height="644" fill="none"
            stroke="var(--frame)" stroke-width="6" stroke-dasharray="10 6"/>
    </svg>

    <p class="line apiary-kicker">Apicoltura</p>
    <h1 class="line apiary-name">Dado sereno</h1>

    <div class="bee-emblem" role="img" aria-label="Line illustration of a bee in honey orange with a honey drop below"></div>

    <h2 class="line honey-type">Millefiori</h2>
    <p class="line origin">Como</p>
    <div class="lake-band" role="img" aria-label="Blue wavy lines suggesting the lake"></div>

    <div class="fill-in weight"><span class="blank"></span><span>g</span></div>
    <div class="fill-in year"><span>Anno</span><span class="blank"></span></div>
  </main>
</body>
</html>
```